Flyer Design Project For Kitchen Rendering Service

We need an A4 Page flyer designed for a new kitchen rendering service we are launching. Our target market is other kitchen designers/manufacturers. We want them to outsource the rendering of their kitchen designs to us. Many kitchen designers still hand draw kitchens using pen and paper. This makes it hard for the end client to visualise how their new kitchen will look. Utilising specialist rendering software we transform hand drawn sketches into photographic quality renders. We provide a few different prospective renders per order giving the customer and their client a complete visualisation of the room.
Here is a few links to examples we would like to showcase.
This is the sketch our client provided: https://www.filmora-vault.net/s/qw8rtbnzx41kplm/Kitchen%20Sketch.pdf
Below is some links to the end result that we provided our client:
https://www.filmora-vault.net/s/h207xqpbnd53wr8/Kitchen%20Brochure%20Sample%2001.jpg
https://www.filmora-vault.net/s/ktaw9pmfrbx2zcy/Kitchen%20Brochure%20Sample%2003.jpg
https://www.filmora-vault.net/s/wep48nbv692hdsa/Kitchen%20Brochure%20Sample%2002.jpg
https://www.filmora-vault.net/s/gmx3rtuzp07yfkc/Kitchen%20Brochure%20Sample%2004.jpg
https://www.filmora-vault.net/s/b6nqwypa2h85jte/Kitchen%20Brochure%20Sample%2005.jpg
Our website for more info is www.hazelgrid.com.au
We only require two things from our client.
1. A drawing of any kind explaining the design (can be sketch, cad, photo, etc).
2. A completed 'Render Information From' That can be downloaded from the photographic render page of our website. http://www.hazelgrid.com.au/#!photographic-rendering/vmtb
The final design should communicate how easy it is for a kitchen designer/manufacturer to transform their basic drawings/sketchs to a photograph quality renders and help them win more jobs and boost sales using our service.
Reason: We have extended the deadline by a few days to allow us to review and provide feedback to some last minute designs that have been submitted. Thank you to all the designers that have submitted designs. Stay tuned for our feedback
Target Market(s)
Our target market is other kitchen designers/manufacturers
Industry/Entity Type
Software
Look and feel
Each slider illustrates characteristics of the customer's brand and the style your logo design should communicate.

```html
<!DOCTYPE html>
<html lang="en">
<head>
<meta charset="utf-8">
<title>Hazelgrid – Kitchen Rendering Flyer</title>
<link rel="stylesheet" href="https://fonts.googleapis.com/css2?family=Roboto:wght@300;400;700&family=Oswald:wght@500;700&display=swap">
<style>
  :root {
    --sky-light: #f4f8fb;
    --sky: #b9d6e8;
    --sky-deep: #8dbbd8;
    --mist: #dbe5ef;
    --brand-blue: #1ba1dc;
    --navy: #1c4f8c;
    --ink: #222428;
    --ink-soft: #3c4046;
    --footer: #5b6e7b;
    --white: #ffffff;
  }
  * { margin: 0; padding: 0; box-sizing: border-box; }
  html, body { width: 849px; height: 1200px; overflow: hidden; background: var(--white); }
  .flyer {
    position: relative; width: 849px; height: 1200px; overflow: hidden;
    font-family: "Roboto", Arial, sans-serif; color: var(--ink);
    background: var(--mist);
  }
  .backdrop { position: absolute; inset: 0; }

  .brand-badge {
    position: absolute; right: -40px; top: -60px; width: 210px; height: 210px;
    border-radius: 50%; background: var(--white); border: 5px solid var(--navy);
    display: flex; align-items: center; justify-content: center; padding: 50px 40px 0 0;
  }
  .brand-name { font-size: 26px; font-weight: 700; color: var(--brand-blue); }

  .headline {
    position: absolute; left: 62px; top: 100px;
    font-weight: 300; font-size: 71px; line-height: 80px; color: var(--ink); letter-spacing: -0.5px;
  }

  .steps { position: absolute; left: 62px; top: 312px; list-style: none; }
  .step { display: flex; align-items: flex-start; margin-bottom: 34px; }
  .step-icon { width: 62px; height: 62px; margin-right: 16px; margin-top: 6px; flex: none; }
  .step-title { font-size: 33px; font-weight: 300; color: var(--brand-blue); line-height: 36px; }
  .step-text { font-size: 15px; color: var(--ink-soft); line-height: 19px; margin-top: 4px; }

  .render {
    position: absolute; border: 9px solid var(--white);
    box-shadow: 0 8px 18px rgba(40, 60, 80, 0.28);
  }
  .render-1 { left: 640px; top: 300px; width: 240px; height: 120px; transform: rotate(9deg);
    background: linear-gradient(160deg, #e8eaeb, #b8bdbf 60%, #8a9092); }
  .render-2 { left: 510px; top: 410px; width: 380px; height: 170px; transform: rotate(8deg);
    background: linear-gradient(170deg, #cfd4d6, #a8b3a4 55%, #5f6a66); }
  .render-3 { left: 385px; top: 555px; width: 500px; height: 270px; transform: rotate(6deg);
    background: linear-gradient(165deg, #e3e5e6, #c3c7c9 50%, #7b8184); }
  .render-4 { left: 150px; top: 655px; width: 485px; height: 320px; transform: rotate(5deg);
    background: linear-gradient(170deg, #d9dcdd, #b7bcbb 45%, #6f7676 80%, #4e5456); }

  .price-box {
    position: absolute; left: 527px; top: 917px; width: 229px; height: 145px;
    background: var(--brand-blue); border: 5px solid var(--white); border-radius: 14px;
    box-shadow: 0 4px 10px rgba(0,0,0,0.18); text-align: center;
  }
  .price { font-family: "Oswald", Arial, sans-serif; font-weight: 700; font-size: 44px; line-height: 50px; color: var(--white); margin-top: 6px; }
  .price-unit { font-family: "Oswald", Arial, sans-serif; font-weight: 500; font-size: 21px; line-height: 24px; color: var(--white); text-align: right; padding-right: 16px; }
  .price-note { font-size: 14.5px; line-height: 19px; color: var(--ink); margin-top: 6px; }

  .intro {
    position: absolute; left: 43px; top: 1022px; width: 420px;
    font-size: 13px; line-height: 19px; color: var(--ink);
  }

  .footer {
    position: absolute; left: 0; top: 1100px; width: 849px; height: 100px;
    background: var(--footer); color: var(--white);
  }
  .company { position: absolute; left: 52px; top: 16px; font-size: 15px; font-weight: 700; line-height: 23px; }
  .company .company-name { font-size: 16px; }
  .company small { font-size: 13.5px; display: block; }
  .social { position: absolute; left: 239px; top: 50px; display: flex; gap: 12px; }
  .social span { width: 32px; height: 32px; border-radius: 7px; background: var(--white); display: block; }
  .call { position: absolute; right: 52px; top: 17px; text-align: right; }
  .call-phone { font-size: 27px; font-weight: 300; line-height: 34px; }
  .call-web { font-size: 20px; font-weight: 700; line-height: 30px; }
</style>
</head>
<body>
<main class="flyer">
  <svg class="backdrop" width="849" height="1200" viewBox="0 0 849 1200" aria-hidden="true">
    <defs>
      <radialGradient id="skyGlow" cx="0.25" cy="0.28" r="0.85">
        <stop offset="0" stop-color="var(--sky-light)"/>
        <stop offset="0.55" stop-color="var(--sky)"/>
        <stop offset="1" stop-color="var(--sky-deep)"/>
      </radialGradient>
    </defs>
    <path d="M0 0 H849 V560 C700 600 560 640 420 660 C260 682 120 690 0 700 Z" fill="url(#skyGlow)"/>
    <ellipse cx="370" cy="985" rx="260" ry="16" fill="#9fb0bf" opacity="0.35"/>
  </svg>

  <div class="brand-badge"><span class="brand-name">Hazelgrid</span></div>

  <h1 class="headline">Quality Design<br>Makes Us Different</h1>

  <ol class="steps">
    <li class="step">
      <svg class="step-icon" viewBox="0 0 62 62" aria-hidden="true">
        <path d="M6 8 H44 V30 M6 8 V54 H48 V40" fill="none" stroke="var(--brand-blue)" stroke-width="5" stroke-linejoin="round"/>
        <path d="M14 42 L48 14 L56 22 L22 50 L12 52 Z" fill="var(--brand-blue)"/>
      </svg>
      <div><p class="step-title">Step : 1</p><p class="step-text">Give us a drawing.<br>(Sketch, CAD, Photo)</p></div>
    </li>
    <li class="step">
      <svg class="step-icon" viewBox="0 0 62 62" aria-hidden="true">
        <path d="M10 4 H40 L52 16 V58 H10 Z" fill="none" stroke="var(--brand-blue)" stroke-width="5" stroke-linejoin="round"/>
        <path d="M22 26 H44 M22 34 H44 M22 42 H44 M28 50 H44" stroke="var(--brand-blue)" stroke-width="4"/>
        <path d="M2 42 L10 52 L22 34" fill="none" stroke="var(--brand-blue)" stroke-width="5" stroke-linecap="round" stroke-linejoin="round"/>
      </svg>
      <div><p class="step-title">Step : 2</p><p class="step-text">Information: Complete our<br>‘render information form’</p></div>
    </li>
    <li class="step">
      <svg class="step-icon" viewBox="0 0 62 62" aria-hidden="true">
        <path d="M31 4 L56 16 V44 L31 58 L6 44 V16 Z M6 16 L31 28 L56 16 M31 28 V58" fill="none" stroke="var(--brand-blue)" stroke-width="5" stroke-linejoin="round"/>
      </svg>
      <div><p class="step-title">Step : 3</p><p class="step-text">We create the 3D images<br>(up to 4 views per kitchen)</p></div>
    </li>
  </ol>

  <div class="render render-1" role="img" aria-label="Kitchen render: sink and benchtop detail"></div>
  <div class="render render-2" role="img" aria-label="Kitchen render: island with rangehoods and garden window"></div>
  <div class="render render-3" role="img" aria-label="Kitchen render: marble island and wall ovens"></div>
  <div class="render render-4" role="img" aria-label="Kitchen render: open kitchen with island, stools and rangehoods"></div>

  <div class="price-box">
    <p class="price">$150-$200</p>
    <p class="price-unit">Per Kitchen</p>
    <p class="price-note">Price varies depending<br>on complexity of kitchen</p>
  </div>

  <p class="intro">We rendered Hazelgrid understands that your kitchen is the heart of your home. This is where families bond as they prepare an I need matter We rendered Hazelgrid understands that your kitchen</p>

  <footer class="footer">
    <div class="company">
      <span class="company-name">Hazelgrid Pty Ltd</span>
      <small>Kirrawee Vale, NSW 2231</small>
      <small>info@hazelgrid.com.au</small>
    </div>
    <div class="social" aria-hidden="true"><span></span><span></span><span></span></div>
    <div class="call">
      <p class="call-phone">Call Now: 0400 555 017</p>
      <p class="call-web">www.hazelgrid.com.au</p>
    </div>
  </footer>
</main>
</body>
</html>
```